IT Company looking to market towards Dental Offices

I am looking for a full-color design. Using my existing logo. Must have High Res stock photos. The brochure needs to be full page edge to edge design single fold pamphlet style. Content provided. Please see the website in attached Word Doc for more content.

```html
<!DOCTYPE html>
<html lang="en">
<head>
<meta charset="utf-8">
<title>Bytewell Tech – Dental Practices Brochure Cover</title>
<link href="https://fonts.googleapis.com/css2?family=Open+Sans:wght@300;400;700;800&display=swap" rel="stylesheet">
<style>
  :root {
    --stage: #e6e7e9;
    --paper: #f4f5f6;
    --brand-blue: #1f6fc2;
    --brand-navy: #1b2a6b;
    --deep-violet: #2e3d8f;
    --sky-blue: #3a88d2;
    --rule-blue: #3b8fd8;
    --ink-muted: #4a4f5a;
    --white: #ffffff;
  }
  * { box-sizing: border-box; margin: 0; padding: 0; }
  html, body {
    width: 1200px; height: 790px; overflow: hidden;
    background: var(--stage);
    font-family: "Open Sans", Arial, sans-serif;
  }
  .brochure-cover {
    position: absolute; left: 338px; top: 25px;
    width: 524px; height: 740px;
    background: var(--paper);
    overflow: hidden;
    box-shadow: 0 4px 18px rgba(0,0,0,0.15);
  }
  .cover-art { position: absolute; inset: 0; }
  .headline {
    position: absolute; left: 275px; top: 162px; width: 230px;
    text-align: center; color: var(--white); line-height: 1.05;
  }
  .headline-lead { font-weight: 300; font-size: 19px; letter-spacing: 0.5px; }
  .headline-offer { font-weight: 800; font-size: 36px; letter-spacing: 1px; }
  .headline-mid { font-weight: 300; font-size: 17px; margin-bottom: 4px; }
  .headline-sector { font-weight: 800; font-size: 25px; letter-spacing: 0.5px; }
  .brand {
    position: absolute; left: 120px; top: 600px;
    display: flex; align-items: center; gap: 16px;
  }
  .brand-dot {
    width: 54px; height: 54px; border-radius: 50%;
    background: var(--brand-blue);
  }
  .brand-name {
    font-weight: 800; font-size: 34px; line-height: 1;
    color: var(--brand-navy);
  }
  .web-address {
    position: absolute; right: 34px; top: 678px;
    display: flex; align-items: center; gap: 7px;
    font-size: 13px; color: var(--ink-muted);
  }
  .web-address strong { color: var(--brand-navy); font-weight: 700; }
  .globe-icon { width: 14px; height: 14px; }
</style>
</head>
<body>
  <main class="brochure-cover">
    <svg class="cover-art" width="524" height="740" viewBox="0 0 524 740">
      <defs>
        <radialGradient id="vault-tones" cx="40%" cy="45%" r="65%">
          <stop offset="0%" stop-color="#c9ccd0"/>
          <stop offset="60%" stop-color="#a9adb3"/>
          <stop offset="100%" stop-color="#8d8a84"/>
        </radialGradient>
      </defs>
      <circle class="photo-ring" cx="180" cy="250" r="292" fill="none" stroke="var(--rule-blue)" stroke-width="1"/>
      <circle class="cover-photo" cx="180" cy="250" r="280" fill="url(#vault-tones)"
              role="img" aria-label="Photograph of a steel bank vault door set into a rough stone wall"/>
      <circle class="accent-main" cx="390" cy="255" r="125" fill="var(--brand-blue)" opacity="0.93"/>
      <circle class="accent-deep" cx="368" cy="405" r="64" fill="var(--deep-violet)" opacity="0.82"/>
      <circle class="accent-light" cx="290" cy="445" r="42" fill="var(--sky-blue)" opacity="0.85"/>
      <line class="footer-rule" x1="0" y1="725" x2="524" y2="708" stroke="var(--rule-blue)" stroke-width="1.5"/>
    </svg>

    <h1 class="headline">
      <span class="headline-lead">Bytewell Tech</span><br>
      <span class="headline-offer">OFFERS</span><br>
      <span class="headline-mid">proven expertise in</span><br>
      <span class="headline-sector">DENTAL</span><br>
      <span class="headline-sector">PRACTICES</span>
    </h1>

    <div class="brand">
      <span class="brand-dot"></span>
      <span class="brand-name">Bytewell Tech</span>
    </div>

    <p class="web-address">
      <svg class="globe-icon" viewBox="0 0 14 14" aria-hidden="true">
        <circle cx="7" cy="7" r="6" fill="none" stroke="var(--brand-blue)" stroke-width="1.3"/>
        <ellipse cx="7" cy="7" rx="2.6" ry="6" fill="none" stroke="var(--brand-blue)" stroke-width="1"/>
        <line x1="1" y1="7" x2="13" y2="7" stroke="var(--brand-blue)" stroke-width="1"/>
      </svg>
      <span>www.<strong>bytewelltech</strong>.com</span>
    </p>
  </main>
</body>
</html>
```